"LuvaWorks" Graphic Design Project

We are a new business creating bath/ body/beauty products. We need label designs for men "Velto for Men " and women- "Velto for Women" . Since the collection called Velto will be used for both- we'd like the labels to look similar but separating the gender look- maybe by a same color variation. Our bottles are amber in color , so we like the beiges, cream, and earthy warm tones - greens- brown-orange- yellow-colors. The labels are for 8 oz amber cosmo round bottles. The height is 7.32inches and the diameter is 1.85 inches.
Our starting line will be Velto for Men ( Silk Body Wash, Silk Body Lotion and Body Mist) and the same for Velto for Women.

Target Market(s)

Our target audience is between 30 to 60 years of age. Salons and private consumers.
I am including attached sample of what was started by me.

Requirements
Must have
• We would like to incorporate the company name- LuvaWorks along with the name of the product- which will be Velto for Men or Velto for Women on each label.

On label with company name or somewhere on label we would like a tree to symbolize the beginning, but we are open to suggestions.

```html
<!DOCTYPE html>
<html lang="en">
<head>
<meta charset="UTF-8">
<title>Velto for Men – Silk Body Wash Label</title>
<link href="https://fonts.googleapis.com/css2?family=Outfit:wght@300;400&display=swap" rel="stylesheet">
<style>
  :root {
    --bg-edge: #d8a67c;
    --bg-mid: #f3e2d0;
    --bg-light: #f8ede2;
    --band: rgba(255, 244, 232, 0.55);
    --brand-orange: #e2a26a;
    --title-brown: #8a6246;
    --info-brown: #7c5c44;
    --meta-brown: #9c7a60;
    --ink: #1f1a16;
    --panel: rgba(255, 250, 244, 0.55);
  }
  * { margin: 0; padding: 0; box-sizing: border-box; }
  html, body { width: 954px; height: 1200px; overflow: hidden; }
  body { font-family: "Outfit", sans-serif; font-weight: 300; }

  .label {
    position: relative;
    width: 954px;
    height: 1200px;
    overflow: hidden;
    background: linear-gradient(180deg, var(--bg-edge) 0%, #e6bd98 18%, var(--bg-mid) 38%, var(--bg-light) 52%, var(--bg-mid) 68%, #e2b58e 88%, var(--bg-edge) 100%);
  }
  .label__pattern {
    position: absolute; inset: 0;
    background: radial-gradient(ellipse at 60% 45%, rgba(255,255,255,0.25), rgba(255,255,255,0) 60%);
  }
  .side-band {
    position: absolute; left: 0; top: 0;
    width: 99px; height: 1200px;
    background: linear-gradient(90deg, rgba(255,246,236,0.35), var(--band) 60%, rgba(255,246,236,0.2));
  }
  .brand-vertical {
    position: absolute;
    left: 49px; top: 598px;
    transform: translate(-50%, -50%) rotate(-90deg);
    font-size: 86px; font-weight: 300;
    color: var(--brand-orange);
    white-space: nowrap; letter-spacing: 0.5px;
  }
  .product-name {
    position: absolute; left: 127px; top: 188px;
    font-size: 82px; font-weight: 400; color: var(--title-brown);
    line-height: 1;
  }
  .product-gender {
    position: absolute; left: 229px; top: 289px;
    font-size: 29px; font-weight: 300; color: var(--title-brown);
    letter-spacing: 0.5px;
  }
  .product-type {
    position: absolute; left: 156px; top: 612px;
    font-size: 33px; font-weight: 300; color: var(--title-brown);
  }
  .description {
    position: absolute; left: 440px; top: 94px; width: 514px;
    text-align: center; color: var(--ink);
    font-size: 22.5px; line-height: 33px;
  }
  .description p { margin-bottom: 32px; }
  .ingredients {
    position: absolute; left: 440px; top: 554px;
    width: 485px; height: 419px;
    border-radius: 22px; background: var(--panel);
    padding: 36px 16px 0;
    text-align: center; color: var(--ink);
    font-size: 18px; line-height: 27.4px;
  }
  .origin {
    position: absolute; left: 147px; top: 1110px; width: 260px;
    text-align: center; color: var(--meta-brown);
    font-size: 23px; line-height: 36px;
  }
  .company {
    position: absolute; left: 453px; top: 1054px; width: 480px;
    text-align: center; color: var(--info-brown);
    font-size: 23.5px; line-height: 32.5px;
  }
</style>
</head>
<body>
<main class="label">
  <div class="label__pattern" role="img" aria-label="Soft warm swirl background pattern"></div>
  <div class="side-band"></div>
  <div class="brand-vertical">LuvaWorks</div>

  <h1 class="product-name">Velto</h1>
  <div class="product-gender">FOR MEN</div>
  <div class="product-type">Silk Body Wash</div>

  <section class="description">
    <p>Our Nourishing Silk Body Wash will engulf you in luxurious lather as it gently cleanses your delicate skin leaving it soft as silk.</p>
    <p>Directions: Apply to skin while damp with sponge or wash cloth. Rinse well.</p>
    <p>WARNINGS/CAUTIONS: For external use only. Avoid contact with eyes.</p>
    <p>NOT TESTED ON ANIMALS</p>
  </section>

  <section class="ingredients">
    INGREDIENTS: purified water, sodium olefin sulfonate (plant source), organic aloe barbadensis leaf juice, cocamidopropyl betaine (plant source), sodium chloride (salt), kosher vegetable glycerin, tocopherol (natural vitamin E), polysorbate 20 (plant source), potassium sorbate (plant source), phenoxyethanol (mild preservative), caprylyl glycol (plant source), organic anthemis nobilis (chamomile) extract, organic calendula officinalis flower extract, xanthan gum (plant source), magnesium ascorbyl phosphate (vitamin C ester), sodium bicarbonate (baking soda), citric acid fragrance.
  </section>

  <div class="origin">
    MADE IN USA<br>8.25 fl oz. / 244mL
  </div>

  <address class="company" style="font-style: normal;">
    LuvaWorks<br>
    Bath – Body - Home<br>
    Coral Bay, FL&nbsp; 33410<br>
    Shop 24/7 - www.luvaworks.com
  </address>
</main>
</body>
</html>
```